m-brightscan needs new website

need to get completely new updated site for m-brightscan.example
general business concepts can be started from that site and I can offer specifick input about business operations and goals. would like to offer on-line ordering, service requests, and payments if possible.

```html
<!DOCTYPE html>
<html lang="en">
<head>
<meta charset="utf-8">
<title>M-BRIGHTSCAN — Imaging Solutions For Your Business</title>
<link rel="stylesheet" href="https://fonts.googleapis.com/css2?family=Source+Sans+3:wght@400;600;700&display=swap">
<style>
  :root {
    --brand-red: #e3001b;
    --ink: #222222;
    --text: #3a3a3a;
    --muted-grey: #8a8a8a;
    --white: #ffffff;
    --card-1: #1b1b1b;
    --card-2: #2a2a2a;
    --card-3: #262626;
    --card-4: #1e1e1e;
    --card-5: #111111;
    --footer-bg: #222222;
    --footer-text: #cfcfcf;
  }
  * { box-sizing: border-box; margin: 0; padding: 0; }
  html, body { width: 1200px; height: 2228px; overflow: hidden; }
  body {
    position: relative;
    background: var(--white);
    font-family: "Source Sans 3", "Source Sans Pro", Arial, sans-serif;
    color: var(--text);
  }
  .container { position: absolute; left: 144px; width: 912px; }

  /* Header */
  .site-header { position: absolute; top: 0; left: 0; width: 1200px; height: 111px; background: var(--white); }
  .brand { position: absolute; left: 144px; top: 34px; display: flex; align-items: center; gap: 10px; }
  .brand-dot { width: 30px; height: 30px; border-radius: 50%; background: var(--brand-red); }
  .brand-name { font-size: 26px; font-weight: 700; color: var(--ink); letter-spacing: .5px; }
  .header-phone { position: absolute; right: 144px; top: 16px; font-size: 23px; color: #777; display: flex; align-items: center; gap: 8px; }
  .main-nav { position: absolute; right: 144px; top: 71px; display: flex; gap: 32px; }
  .main-nav a { font-size: 16px; font-weight: 600; text-transform: uppercase; color: var(--ink); text-decoration: none; }
  .main-nav a.active { color: var(--brand-red); }

  /* Hero */
  .hero { position: absolute; top: 111px; left: 0; width: 1200px; height: 502px; }
  .hero-photo { position: absolute; inset: 0; background: linear-gradient(180deg, #c9ccd0 0%, #a9a39e 40%, #6b6460 75%, #2b2b2d 100%); }
  .hero-title { position: absolute; left: 0; right: 0; top: 436px; text-align: center; font-size: 40px; font-weight: 600; color: var(--white); }
  .slider-arrow { position: absolute; top: 232px; width: 32px; height: 38px; background: var(--brand-red); display: flex; align-items: center; justify-content: center; }
  .slider-arrow.prev { left: 47px; }
  .slider-arrow.next { right: 50px; }

  /* Intro */
  .intro { top: 686px; text-align: center; }
  .intro p { font-size: 20px; line-height: 32px; color: var(--text); }
  .btn { display: inline-block; background: var(--brand-red); color: var(--white); font-size: 14px; text-transform: uppercase; text-decoration: none; padding: 0 18px; height: 40px; line-height: 40px; }
  .intro .btn { margin-top: 25px; }

  /* Services */
  .services { top: 913px; display: grid; grid-template-columns: repeat(3, 304px); grid-auto-rows: 300px; }
  .service-card { position: relative; padding: 27px 22px 0; color: var(--white); }
  .service-card:nth-child(1) { background: var(--brand-red); }
  .service-card:nth-child(2) { background: var(--card-1); }
  .service-card:nth-child(3) { background: var(--card-2); }
  .service-card:nth-child(4) { background: var(--card-3); }
  .service-card:nth-child(5) { background: var(--card-4); }
  .service-card:nth-child(6) { background: var(--card-5); }
  .service-icon { width: 80px; height: 80px; border-radius: 50%; background: radial-gradient(circle, #9a9a9a 0%, #d9d9d9 45%, #ffffff 70%); }
  .service-rule { width: 116px; height: 4px; background: #6e6e6e; margin-top: 27px; }
  .service-card:nth-child(1) .service-rule { background: var(--white); }
  .service-title { margin-top: 16px; font-size: 21px; line-height: 24px; font-weight: 700; text-transform: uppercase; }
  .service-text { position: absolute; left: 22px; right: 22px; top: 212px; font-size: 11.5px; line-height: 18px; color: var(--muted-grey); }
  .service-card:nth-child(1) .service-text { color: var(--white); font-weight: 600; }

  /* Mission */
  .mission { position: absolute; top: 1594px; left: 0; width: 1200px; height: 300px; }
  .mission-photo { position: absolute; inset: 0; background: linear-gradient(180deg, #5b5d62 0%, #4a4b50 45%, #6a625c 80%, #8a7f76 100%); }
  .mission-content { position: absolute; left: 0; right: 0; top: 66px; text-align: center; color: var(--white); }
  .mission-content h2 { font-size: 40px; line-height: 46px; font-weight: 700; }
  .mission-content p { font-size: 19px; line-height: 25px; margin: 2px auto 0; width: 900px; }
  .mission-content .btn { margin-top: 16px; }

  /* Contact */
  .contact { top: 1960px; }
  .contact h2 { text-align: center; font-size: 40px; font-weight: 700; color: var(--brand-red); }
  .contact-row { display: flex; justify-content: space-between; margin-top: 18px; font-size: 19px; color: var(--text); }
  .contact-item { display: flex; align-items: center; gap: 8px; }

  /* Footer */
  .site-footer { position: absolute; top: 2131px; left: 0; width: 1200px; height: 97px; background: var(--footer-bg); }
  .footer-nav { position: absolute; left: 144px; top: 22px; font-size: 12px; color: var(--footer-text); }
  .footer-nav a { color: var(--footer-text); text-decoration: none; }
  .footer-nav .sep { margin: 0 12px; }
  .copyright { position: absolute; left: 144px; top: 54px; font-size: 12px; color: var(--footer-text); }
  .social { position: absolute; right: 144px; top: 40px; display: flex; gap: 16px; }
  .social span { width: 14px; height: 14px; border-radius: 50%; background: #bdbdbd; }
</style>
</head>
<body>

<header class="site-header">
  <div class="brand"><span class="brand-dot"></span><span class="brand-name">M-BRIGHTSCAN</span></div>
  <div class="header-phone">
    <svg width="18" height="18" viewBox="0 0 24 24"><path fill="#777" d="M6.6 10.8a15.1 15.1 0 0 0 6.6 6.6l2.2-2.2c.3-.3.7-.4 1-.2 1.1.4 2.3.6 3.6.6.6 0 1 .4 1 1V20c0 .6-.4 1-1 1A17 17 0 0 1 3 4c0-.6.4-1 1-1h3.5c.6 0 1 .4 1 1 0 1.3.2 2.5.6 3.6.1.3 0 .7-.2 1z"/></svg>
    555 014 2287
  </div>
  <nav class="main-nav">
    <a class="active" href="#">Home</a>
    <a href="#">About Us</a>
    <a href="#">Our Services</a>
    <a href="#">Applications</a>
    <a href="#">Contact</a>
  </nav>
</header>

<section class="hero">
  <div class="hero-photo" role="img" aria-label="Photo of business people meeting in a bright office"></div>
  <a class="slider-arrow prev" href="#" aria-label="Previous slide"><svg width="14" height="18" viewBox="0 0 14 18"><path d="M10 2 4 9l6 7" fill="none" stroke="#fff" stroke-width="3"/></svg></a>
  <a class="slider-arrow next" href="#" aria-label="Next slide"><svg width="14" height="18" viewBox="0 0 14 18"><path d="M4 2l6 7-6 7" fill="none" stroke="#fff" stroke-width="3"/></svg></a>
  <h1 class="hero-title">Imaging Solutions For Your Business</h1>
</section>

<section class="container intro">
  <p>M-BRIGHTSCAN strives to be the leading provider of cost-effective solutions to the Retail, Wholesale and Banking Marketplace. Our experience in supplying complete software, hardware, and turnkey systems enables us to provide a system that fits your needs, we don't believe in trying to change your operations to fit our products.</p>
  <a class="btn" href="#">Read More</a>
</section>

<section class="container services">
  <article class="service-card">
    <div class="service-icon" role="img" aria-label="Product image of a multifunction printer"></div>
    <div class="service-rule"></div>
    <h3 class="service-title">Branch<br>Transformation</h3>
    <p class="service-text">Vivamus eleifend vitae nulla vel malesuada. In ac malesuada lacus, et consectetur ante. Fusce vitae lectus sit amet mi pulvinar maximus.</p>
  </article>
  <article class="service-card">
    <div class="service-icon" role="img" aria-label="Product image of a cheque scanner"></div>
    <div class="service-rule"></div>
    <h3 class="service-title">Teller Image Capture</h3>
    <p class="service-text">Phasellus nisl est, condimentum vitae faucibus in, sollicitudin vel metus. Nunc sit amet consequat risus. Curabitur ac elit leo. In eleifend dui.</p>
  </article>
  <article class="service-card">
    <div class="service-icon" role="img" aria-label="Product image of an office copier"></div>
    <div class="service-rule"></div>
    <h3 class="service-title">Branch Image Capture</h3>
    <p class="service-text">Integer eu massa lacinia, lacinia nulla non, volutpat purus. Sed libero felis, vestibulum et dolor eget, lacinia aliquet neque.</p>
  </article>
  <article class="service-card">
    <div class="service-icon" role="img" aria-label="Product image of a desktop printer"></div>
    <div class="service-rule"></div>
    <h3 class="service-title">Remote Deposite<br>Capture</h3>
    <p class="service-text">Aenean sed quam non sapien faucibus consequat vitae sit amet orci. Praesent quis risus mi. In mollis nulla in pulvinar dictum.</p>
  </article>
  <article class="service-card">
    <div class="service-icon" role="img" aria-label="Product image of a point of sale scanner"></div>
    <div class="service-rule"></div>
    <h3 class="service-title">Point of Sale Capture</h3>
    <p class="service-text">Aenean faucibus lacus ut mollis commodo. Donec vestibulum odio sem, ac laoreet massa ullamcorper id. Donec molestie nisi et tellus.</p>
  </article>
  <article class="service-card">
    <div class="service-icon" role="img" aria-label="Product image of a lockbox document scanner"></div>
    <div class="service-rule"></div>
    <h3 class="service-title">Lockbox</h3>
    <p class="service-text">Nunc eu ligula sed quam pulvinar maximus in vitae eros. Proin porta fermentum ipsum, vel porttitor turpis venenatis luctus.</p>
  </article>
</section>

<section class="mission">
  <div class="mission-photo" role="img" aria-label="Blurred photo of a busy bank lobby"></div>
  <div class="mission-content">
    <h2>Our Mission</h2>
    <p>M-BRIGHTSCAN strives to be the leading provider of cost-effective software, hardware, and turnkey solutions to the Business, Utility, and Banking Marketplace.</p>
    <a class="btn" href="#">Read More</a>
  </div>
</section>

<section class="container contact">
  <h2>Contact Us</h2>
  <div class="contact-row">
    <div class="contact-item">
      <svg width="12" height="18" viewBox="0 0 12 18"><path fill="#3a3a3a" d="M6 0a6 6 0 0 0-6 6c0 4.5 6 12 6 12s6-7.5 6-12a6 6 0 0 0-6-6zm0 8.5A2.5 2.5 0 1 1 6 3.5a2.5 2.5 0 0 1 0 5z"/></svg>
      24 Building name, Street name, City Zipcode
    </div>
    <div class="contact-item">
      <svg width="16" height="16" viewBox="0 0 24 24"><path fill="#3a3a3a" d="M6.6 10.8a15.1 15.1 0 0 0 6.6 6.6l2.2-2.2c.3-.3.7-.4 1-.2 1.1.4 2.3.6 3.6.6.6 0 1 .4 1 1V20c0 .6-.4 1-1 1A17 17 0 0 1 3 4c0-.6.4-1 1-1h3.5c.6 0 1 .4 1 1 0 1.3.2 2.5.6 3.6.1.3 0 .7-.2 1z"/></svg>
      555 019 7743
    </div>
    <div class="contact-item">
      <svg width="18" height="14" viewBox="0 0 18 14"><path fill="#3a3a3a" d="M0 0h18v2L9 8 0 2zM0 4l9 6 9-6v10H0z"/></svg>
      info@m-brightscan.example
    </div>
  </div>
</section>

<footer class="site-footer">
  <nav class="footer-nav">
    <a href="#">Home</a><span class="sep">|</span><a href="#">About Us</a><span class="sep">|</span><a href="#">Our Services</a><span class="sep">|</span><a href="#">Applications</a><span class="sep">|</span><a href="#">Contact</a>
  </nav>
  <p class="copyright">Copyright &copy; 2019 &nbsp;M-Brightscan Imaging. &nbsp;All rights reserved.</p>
  <div class="social" aria-label="Social links"><span></span><span></span></div>
</footer>

</body>
</html>
```